Healthy lifestyle Influencer business card

I need your creativity to have a business card that I can leave in all the restaurants, hotels and spas I visit to inform them that I am an influencer specializing in the wellness sector and that I will write a review about them. You can use my instagram photos Lunavita27 or on my website www.piattileggeriorto.it. I would like my business card to impress with its creativity! thank you very much!

Contact Information for Business Card

siteweb, instagram, phone number

Font styles to use
Decorative
Script

Colors
0094D4
00A9DD
6FCCEA
C7EBF8
E9F6FB
59FF00
82FF00
B8FF75
E3FFCB
F4FFEA
FFC000
F8CF3A
FAE287
FDF2CF
FEFAEE
F0912C
F2A743
F7CA91
FBE8D2
FDF5EE
EE7325
F08F49
F5BC92
FAE3D3
FDF4ED
EB3D1F
EC4F4E
F09395
F8D3D4
FCEDEE
E54698
E96AAD
F1A4CE
F9D9EA
FCEFF6

Requirements
Nice to have
• creativity

```html
<!DOCTYPE html>
<html lang="it">
<head>
<meta charset="utf-8">
<title>Luna Vita Chef – Biglietto da visita</title>
<link rel="stylesheet" href="https://fonts.googleapis.com/css2?family=Great+Vibes&family=Jost:wght@400&family=Roboto:wght@300;400&display=swap">
<style>
  :root {
    --backdrop: #2a2a2a;
    --mint: #93b8ae;
    --charcoal: #464646;
    --charcoal-light: #555555;
    --ink: #4a4a4a;
    --paper: #f1f1ef;
  }
  html, body {
    margin: 0;
    padding: 0;
    width: 1138px;
    height: 1200px;
    overflow: hidden;
    background: var(--backdrop);
  }
  .canvas {
    position: relative;
    width: 1138px;
    height: 1200px;
  }
  .card {
    position: absolute;
    border-radius: 16px;
    overflow: hidden;
  }
  .card--front {
    left: 158px; top: 274px; width: 374px; height: 618px;
    background: var(--mint);
    color: var(--ink);
  }
  .card--back {
    left: 578px; top: 272px; width: 376px; height: 622px;
    background: linear-gradient(160deg, var(--charcoal) 0%, var(--charcoal-light) 100%);
    color: var(--paper);
  }
  .brand-name {
    font-family: "Great Vibes", cursive;
    font-weight: 400;
    white-space: nowrap;
    line-height: 1;
  }
  .tagline {
    font-family: "Jost", sans-serif;
    font-weight: 400;
    white-space: nowrap;
    line-height: 1;
  }
  .front-lockup {
    position: absolute;
    left: 190px; top: 290px;
    transform: translate(-50%, -50%) rotate(-90deg);
    text-align: center;
  }
  .front-lockup .brand-name { font-size: 60px; color: var(--ink); }
  .front-lockup .tagline { font-size: 18px; color: var(--ink); margin-top: 4px; }

  .back-lockup {
    position: absolute;
    left: 0; right: 0; top: 126px;
    text-align: center;
  }
  .back-lockup .brand-name { font-size: 54px; color: var(--paper); }
  .back-lockup .tagline { font-size: 17px; color: var(--paper); margin-top: 10px; }

  .person-name {
    position: absolute;
    left: 0; right: 0; top: 318px;
    text-align: center;
    font-family: "Great Vibes", cursive;
    font-size: 42px;
    line-height: 1;
    color: var(--paper);
  }
  .contact-divider {
    position: absolute;
    left: 74px; top: 388px;
  }
  .contact-list {
    position: absolute;
    left: 0; right: 0; top: 434px;
    margin: 0; padding: 0;
    list-style: none;
    text-align: center;
    font-family: "Roboto", sans-serif;
    font-weight: 300;
    font-size: 16px;
    line-height: 24px;
    color: var(--paper);
  }
  .social-handle {
    position: absolute;
    left: 0; right: 0;
    display: flex;
    justify-content: center;
    align-items: center;
    gap: 10px;
    font-family: "Roboto", sans-serif;
    font-weight: 400;
    font-size: 16px;
  }
  .card--front .social-handle { top: 566px; color: var(--ink); }
  .card--back .social-handle { top: 570px; color: var(--paper); }
  .social-dot {
    width: 12px; height: 12px;
    border-radius: 50%;
    background: currentColor;
  }
</style>
</head>
<body>
<main class="canvas">

  <section class="card card--front" aria-label="Fronte del biglietto">
    <div class="front-lockup">
      <div class="brand-name">Luna Vita Chef</div>
      <div class="tagline">Benessere a ogni assaggio</div>
    </div>
    <div class="social-handle"><span class="social-dot"></span>@Lunavita27</div>
  </section>

  <section class="card card--back" aria-label="Retro del biglietto">
    <div class="back-lockup">
      <div class="brand-name">Luna Vita Chef</div>
      <div class="tagline">Benessere a ogni assaggio</div>
    </div>

    <div class="person-name">Luna Ferretti</div>

    <svg class="contact-divider" width="230" height="28" viewBox="0 0 230 28" aria-hidden="true">
      <line x1="0" y1="14" x2="62" y2="14" stroke="#e6e6e6" stroke-width="1.6"/>
      <line x1="164" y1="14" x2="228" y2="14" stroke="#e6e6e6" stroke-width="1.6"/>
      <g fill="#8fb7ad" stroke="#d8e8e3" stroke-width="1">
        <circle cx="87" cy="14" r="11"/>
        <circle cx="114" cy="14" r="11"/>
        <circle cx="141" cy="14" r="11"/>
      </g>
      <g fill="none" stroke="#3e4a47" stroke-width="1.2">
        <path d="M82 11 q5 -4 10 0 v2 h-2 v-1 h-6 v1 h-2 z M83 14 h8 v5 h-8 z"/>
        <rect x="108" y="10" width="12" height="8"/>
        <path d="M108 10 l6 5 l6 -5"/>
        <circle cx="141" cy="14" r="6"/>
        <ellipse cx="141" cy="14" rx="2.5" ry="6"/>
        <line x1="135" y1="14" x2="147" y2="14"/>
      </g>
    </svg>

    <ul class="contact-list">
      <li>000-0000-0000</li>
      <li>info@piattileggeriorto.it</li>
      <li>www.piattileggeriorto.it</li>
    </ul>

    <div class="social-handle"><span class="social-dot"></span>@Lunavita27</div>
  </section>

</main>
</body>
</html>
```